Whitcombe Business Card Design

The name of the business is Dario Whitcombe, CPA LLC
The service that we offer is Accounting, Tax & Consulting Services. I need it to have the following items:
Dario Whitcombe, Principal
Phone Number
Email Address
Physical Address

I have attached the company logo, one in black and one in white. Please provide a design in black background and the other in white background. Please include "Accounting, Tax & Consulting Services". I want the business card to be clean and very professional.

```html
<!DOCTYPE html>
<html lang="en">
<head>
<meta charset="UTF-8">
<title>Dario Whitcombe, CPA LLC — Business Cards</title>
<link href="https://fonts.googleapis.com/css2?family=Montserrat:wght@600;700&family=Roboto:wght@300;400&display=swap" rel="stylesheet">
<style>
  :root {
    --stage: #2a2a2a;
    --card-dark: #1f1f21;
    --card-dark-2: #29292b;
    --card-light: #f4f4f4;
    --card-light-2: #e4e4e6;
    --brand-red: #8c1419;
    --accent-red: #a3161c;
    --silver: #9a9a9c;
    --text-light: #e6e6e6;
    --text-muted: #8d8d90;
    --text-dark: #2a2a2c;
  }
  * { margin: 0; padding: 0; box-sizing: border-box; }
  html, body { width: 1200px; height: 1138px; overflow: hidden; }
  body { background: var(--stage); position: relative; font-family: "Roboto", sans-serif; }

  .card {
    position: absolute;
    border-radius: 16px;
    overflow: hidden;
    box-shadow: 0 6px 14px rgba(0,0,0,0.45);
  }

  /* Front: white-background version */
  .card--front {
    left: 272px; top: 184px; width: 622px; height: 376px;
    background: linear-gradient(160deg, var(--card-light) 0%, var(--card-light-2) 100%);
    display: flex; flex-direction: column; align-items: center; justify-content: center;
    gap: 22px;
  }
  .front-wordmark {
    font-family: "Montserrat", sans-serif;
    font-weight: 700;
    font-size: 36px;
    letter-spacing: 3px;
    color: var(--text-dark);
    text-transform: uppercase;
    text-align: center;
    line-height: 1.2;
  }
  .front-services {
    font-family: "Montserrat", sans-serif;
    font-weight: 600;
    font-size: 13px;
    letter-spacing: 2px;
    color: var(--accent-red);
    text-transform: uppercase;
  }

  /* Back: black-background version */
  .card--back {
    left: 274px; top: 606px; width: 619px; height: 375px;
    background: linear-gradient(160deg, var(--card-dark-2) 0%, var(--card-dark) 100%);
  }
  .back-shape { position: absolute; inset: 0; }
  .back-wordmark {
    position: absolute; left: 24px; top: 150px; width: 200px;
    font-family: "Montserrat", sans-serif;
    font-weight: 700; font-size: 26px; line-height: 1.25;
    letter-spacing: 1px;
    color: #ffffff; text-transform: uppercase;
  }

  .info { position: absolute; right: 27px; text-align: right; white-space: nowrap; }
  .firm-name {
    top: 36px;
    font-family: "Montserrat", sans-serif; font-weight: 600;
    font-size: 19px; letter-spacing: 0.5px;
    color: var(--text-light); text-transform: uppercase;
  }
  .firm-tagline {
    top: 62px;
    font-family: "Montserrat", sans-serif; font-weight: 600;
    font-size: 13px; letter-spacing: 2px;
    color: var(--text-muted); text-transform: uppercase;
  }
  .firm-services {
    top: 84px;
    font-weight: 300; font-size: 13px; letter-spacing: 0.5px;
    color: var(--text-light);
  }
  .person-name {
    top: 150px;
    font-family: "Montserrat", sans-serif; font-weight: 700;
    font-size: 19px; letter-spacing: 0.5px;
    color: var(--accent-red); text-transform: uppercase;
  }
  .person-title { top: 177px; font-weight: 300; font-size: 16px; color: var(--text-light); }
  .address { top: 226px; font-weight: 300; font-size: 16px; line-height: 24px; color: var(--text-light); }

  .contact { position: absolute; right: 27px; top: 281px; list-style: none; }
  .contact li {
    display: flex; align-items: center; justify-content: flex-end; gap: 14px;
    font-weight: 300; font-size: 16px; color: var(--text-light); height: 24px;
  }
  .contact svg { width: 13px; height: 13px; fill: var(--accent-red); flex: none; }
</style>
</head>
<body>

  <section class="card card--front" aria-label="Business card, white background">
    <div class="front-wordmark">Dario<br>Whitcombe</div>
    <div class="front-services">Accounting, Tax &amp; Consulting Services</div>
  </section>

  <section class="card card--back" aria-label="Business card, black background">
    <svg class="back-shape" width="619" height="375" viewBox="0 0 619 375" aria-hidden="true">
      <path d="M0,0 H214 Q342,187 206,375 H0 Z" fill="var(--silver)"/>
      <path d="M0,0 H204 Q325,187 199,375 H0 Z" fill="var(--brand-red)"/>
    </svg>
    <div class="back-wordmark">Dario<br>Whitcombe</div>

    <div class="info firm-name">Dario Whitcombe, CPA LLC</div>
    <div class="info firm-tagline">Certified Public Accountant</div>
    <div class="info firm-services">Accounting, Tax &amp; Consulting Services</div>
    <div class="info person-name">Dario Whitcombe</div>
    <div class="info person-title">Principal</div>
    <div class="info address">4820 Harbor Lane, Millbrook,<br>Fairview County, US 204817</div>

    <ul class="contact">
      <li>555-201-4830
        <svg viewBox="0 0 24 24" aria-hidden="true"><path d="M6.6 10.8a15 15 0 0 0 6.6 6.6l2.2-2.2a1 1 0 0 1 1-.25 11.4 11.4 0 0 0 3.6.6 1 1 0 0 1 1 1V20a1 1 0 0 1-1 1A17 17 0 0 1 3 4a1 1 0 0 1 1-1h3.5a1 1 0 0 1 1 1c0 1.25.2 2.45.6 3.6a1 1 0 0 1-.25 1z"/></svg>
      </li>
      <li>dw@whitcombecpa.com
        <svg viewBox="0 0 24 24" aria-hidden="true"><path d="M2 5h20v14H2z"/><path d="M2 5l10 8 10-8" fill="none" stroke="#1f1f21" stroke-width="2"/></svg>
      </li>
      <li>www.whitcombecpa.com
        <svg viewBox="0 0 24 24" aria-hidden="true"><circle cx="12" cy="12" r="10"/></svg>
      </li>
    </ul>
  </section>

</body>
</html>
```